Business Card for Coastal Tundrabridge Advisory

We need a business card for Coastal Tundrabridge Advisory. The company website address is provided below. The company logo is attached. We provide specialized permafrost services to the mining, transportation, and oil & gas industries. The card should be prepared for:
Matthias Korhonen, PhD.
Coastal Tundrabridge Advisory
PO Box 418259
Quillwater, Alaska 99642
Direct: +1-907-555-0143
Email: mkorhonen@tundrabridgeadvisory.example
Website: www.coastaltundrabridgeadvisory.example

```html
<!DOCTYPE html>
<html lang="en">
<head>
<meta charset="utf-8">
<title>Coastal Tundrabridge Advisory — Business Card</title>
<link rel="stylesheet" href="https://fonts.googleapis.com/css2?family=Roboto+Condensed:ital,wght@0,400;0,700;1,700&display=swap">
<style>
  :root {
    --backdrop: #eeeeee;
    --card-white: #ffffff;
    --band-grey: #7f7f7f;
    --band-dark: #363636;
    --ink: #1e1e1e;
    --ink-soft: #2b2b2b;
    --on-grey: #ffffff;
    --card-back: #333333;
    --gold: #8c7b3c;
  }
  * { margin: 0; padding: 0; box-sizing: border-box; }
  html, body {
    width: 1200px; height: 1200px; overflow: hidden;
    background: var(--backdrop);
    font-family: "Roboto Condensed", "Arial Narrow", sans-serif;
  }
  .card {
    position: absolute; left: 235px;
    width: 726px; height: 415px;
    border-radius: 28px; overflow: hidden;
  }
  .card--front { top: 152px; background: var(--card-white); }
  .card--back { top: 650px; background: var(--card-back); }

  .front-bands { position: absolute; inset: 0; width: 100%; height: 100%; }
  .front-bands .band-grey { fill: var(--band-grey); }
  .front-bands .band-dark { fill: var(--band-dark); }

  .company-name {
    position: absolute; left: 39px; top: 62px; width: 300px;
    font-weight: 700; font-size: 24px; line-height: 1.05;
    text-transform: uppercase; letter-spacing: 1px; color: var(--ink);
  }
  .holder { position: absolute; left: 438px; top: 63px; color: var(--ink); }
  .holder-name { font-weight: 700; font-style: italic; font-size: 18px; }
  .holder-title { font-size: 16px; margin-top: 3px; }

  .contact-line {
    position: absolute; display: flex; align-items: center; gap: 7px;
    color: var(--on-grey); font-size: 16px; white-space: nowrap;
  }
  .contact-icon { width: 18px; height: 18px; flex: none; }
  .contact-icon circle { fill: var(--on-grey); }
  .contact-icon .glyph { fill: none; stroke: var(--band-grey); stroke-width: 1.4; stroke-linecap: round; stroke-linejoin: round; }

  .address {
    position: absolute; left: 57px; top: 350px;
    font-size: 16px; line-height: 26px; color: var(--ink-soft);
  }

  .back-name {
    position: absolute; left: 0; right: 0; top: 180px; text-align: center;
    font-weight: 700; font-size: 40px; letter-spacing: 2px;
    text-transform: uppercase; color: var(--gold);
  }
</style>
</head>
<body>

<section class="card card--front" aria-label="Business card front">
  <svg class="front-bands" viewBox="0 0 525 300" preserveAspectRatio="none" aria-hidden="true">
    <polygon class="band-grey" points="293,97 525,97 525,245 148,245 120,226 165,226"/>
    <polygon class="band-dark" points="0,190 199,190 165,226 0,226"/>
  </svg>

  <div class="company-name">Coastal Tundrabridge Advisory</div>

  <div class="holder">
    <div class="holder-name">Matthias Korhonen, PhD</div>
    <div class="holder-title">Founder &amp; Director</div>
  </div>

  <div class="contact-line" style="left:410px; top:157px;">
    <svg class="contact-icon" viewBox="0 0 18 18" aria-hidden="true"><circle cx="9" cy="9" r="9"/><path class="glyph" d="M6 5 L7.5 5 L8.3 7.2 L7.3 8 Q8 10 10 10.7 L10.8 9.7 L13 10.5 L13 12 Q9 12.5 6.8 10 Q5 8 6 5 Z"/></svg>
    <span>+1-907-555-0143</span>
  </div>
  <div class="contact-line" style="left:381px; top:185px;">
    <svg class="contact-icon" viewBox="0 0 18 18" aria-hidden="true"><circle cx="9" cy="9" r="9"/><rect class="glyph" x="6.3" y="4.3" width="5.4" height="9.4" rx="1"/></svg>
    <span>(907) 555 0187</span>
  </div>
  <div class="contact-line" style="left:353px; top:214px;">
    <svg class="contact-icon" viewBox="0 0 18 18" aria-hidden="true"><circle cx="9" cy="9" r="9"/><rect class="glyph" x="4.8" y="6" width="8.4" height="6" rx="0.6"/><path class="glyph" d="M4.8 6.3 L9 9.4 L13.2 6.3"/></svg>
    <span>mkorhonen@tundrabridgeadvisory.example</span>
  </div>
  <div class="contact-line" style="left:326px; top:243px;">
    <svg class="contact-icon" viewBox="0 0 18 18" aria-hidden="true"><circle cx="9" cy="9" r="9"/><circle class="glyph" cx="9" cy="9" r="4.5" style="fill:none"/><path class="glyph" d="M4.5 9 H13.5 M9 4.5 Q6.5 9 9 13.5 M9 4.5 Q11.5 9 9 13.5"/></svg>
    <span>www.coastaltundrabridgeadvisory.example</span>
  </div>

  <address class="address" style="font-style:normal;">
    PO Box 418259<br>
    Quillwater, Alaska 99642
  </address>
</section>

<section class="card card--back" aria-label="Business card back">
  <div class="back-name">Coastal Tundrabridge Advisory</div>
</section>

</body>
</html>
```